"Vine Hollow Excursions" is a top notch Santa Barbara County Wine Tour company.

We provide scenic, boutique and custom wine tours. I need the card to be clean and classy. I will provide our logo. I would like the logo to cover the back side of the card as an option and would like to see a couple color options other then our signature green and gold. I would like to see some creative options and let the designers come up with options.
I need cards for myself and my team. The final design should communicate "An authentic and boutique wine tour experience"
Please use my website for reference www.vinehollowexcursions.example

Target Market(s)

We have a wide range of clients from millennials to baby boomers

Industry/Entity Type

Tour

Contact Information for Business Card

Contact info:
Dale Morton
805-219-6384
info@vinehollowexcursions.example
vinehollowexcursions.example

Colors

Designer to choose colors to be used in the design.

Requirements
Must have
• my logo
Nice to have
• *I would like to have the backside side with the logo and the company statement
• "An authentic and boutique wine tour experience" as an option.
• *I would also like to see what the designers can create!
• *I would like to see an option that incorporates or social: instagram, yelp, Trip Planner
Should not have
• I do not want it too busy.

```html
<!DOCTYPE html>
<html lang="en">
<head>
<meta charset="utf-8">
<title>Vine Hollow Excursions – Business Card</title>
<link href="https://fonts.googleapis.com/css2?family=Roboto:wght@400;500;700&display=swap" rel="stylesheet">
<style>
  :root {
    --stage: #2b2b2b;
    --card-white: #ffffff;
    --card-black: #161616;
    --vine-green: #1f6b3a;
    --gold: #a68a64;
    --ink: #555555;
  }
  * { margin: 0; padding: 0; box-sizing: border-box; }
  html, body { width: 1200px; height: 900px; overflow: hidden; }
  body {
    background: var(--stage);
    font-family: "Roboto", Arial, sans-serif;
    position: relative;
  }
  .card {
    position: absolute;
    width: 520px;
    height: 300px;
    border-radius: 22px;
    overflow: hidden;
  }
  .card-front { left: 60px; top: 400px; background: var(--card-white); }
  .card-back { left: 620px; top: 200px; background: var(--card-black); }

  .front-wave { position: absolute; inset: 0; }

  .holder { position: absolute; left: 38px; top: 46px; }
  .holder-name {
    color: var(--vine-green);
    font-size: 30px;
    font-weight: 500;
    letter-spacing: 0.5px;
    text-transform: uppercase;
  }
  .holder-title {
    color: var(--gold);
    font-size: 15px;
    font-weight: 700;
    letter-spacing: 0.6px;
    text-transform: uppercase;
    margin-top: 4px;
    padding-left: 26px;
  }

  .divider {
    position: absolute;
    left: 205px;
    top: 108px;
    width: 1.5px;
    height: 78px;
    background: var(--gold);
  }

  .contact-list {
    position: absolute;
    left: 216px;
    top: 116px;
    list-style: none;
  }
  .contact-item {
    display: flex;
    align-items: center;
    gap: 6px;
    color: var(--ink);
    font-size: 12.5px;
    line-height: 18px;
    white-space: nowrap;
  }
  .contact-icon {
    width: 11px;
    height: 11px;
    flex: none;
  }

  .brand-lockup {
    position: absolute;
    inset: 0;
    display: flex;
    align-items: center;
    justify-content: center;
    gap: 14px;
  }
  .brand-dot {
    width: 34px;
    height: 34px;
    border-radius: 50%;
    background: var(--vine-green);
  }
  .brand-name {
    color: var(--gold);
    font-size: 26px;
    font-weight: 500;
    letter-spacing: 2px;
    text-transform: uppercase;
  }
</style>
</head>
<body>

  <section class="card card-front">
    <svg class="front-wave" viewBox="0 0 520 300" width="520" height="300" aria-hidden="true">
      <path d="M0,122 C70,150 110,262 310,300 L0,300 Z" fill="var(--vine-green)"/>
      <path d="M0,110 C78,140 120,250 336,300" fill="none" stroke="var(--gold)" stroke-width="6"/>
    </svg>

    <div class="holder">
      <h1 class="holder-name">Dale Morton</h1>
      <p class="holder-title">Trip Planner</p>
    </div>

    <div class="divider"></div>

    <ul class="contact-list">
      <li class="contact-item">
        <svg class="contact-icon" viewBox="0 0 12 12"><circle cx="6" cy="6" r="6" fill="var(--vine-green)"/><path d="M4,3 L5,3 L5.6,4.6 L4.9,5.2 Q5.6,6.6 6.8,7.1 L7.4,6.4 L9,7 L9,8 Q8.6,9 7.6,9 Q4.4,8.6 3,4.4 Q3,3.4 4,3 Z" fill="#fff"/></svg>
        805-219-6384
      </li>
      <li class="contact-item">
        <svg class="contact-icon" viewBox="0 0 12 12"><circle cx="6" cy="6" r="6" fill="var(--vine-green)"/><rect x="3" y="4" width="6" height="4.2" fill="none" stroke="#fff" stroke-width="0.9"/><path d="M3,4 L6,6.4 L9,4" fill="none" stroke="#fff" stroke-width="0.9"/></svg>
        info@vinehollowexcursions.example
      </li>
      <li class="contact-item">
        <svg class="contact-icon" viewBox="0 0 12 12"><circle cx="6" cy="6" r="6" fill="var(--vine-green)"/><circle cx="6" cy="6" r="3.2" fill="none" stroke="#fff" stroke-width="0.8"/><path d="M2.8,6 H9.2 M6,2.8 Q4.4,6 6,9.2 M6,2.8 Q7.6,6 6,9.2" fill="none" stroke="#fff" stroke-width="0.7"/></svg>
        www.vinehollowexcursions.example
      </li>
      <li class="contact-item">
        <svg class="contact-icon" viewBox="0 0 12 12"><circle cx="6" cy="6" r="6" fill="var(--vine-green)"/></svg>
        www.facepage.example/vinehollow
      </li>
      <li class="contact-item">
        <svg class="contact-icon" viewBox="0 0 12 12"><circle cx="6" cy="6" r="6" fill="var(--vine-green)"/></svg>
        www.chirp.example/vinehollowtours
      </li>
      <li class="contact-item">
        <svg class="contact-icon" viewBox="0 0 12 12"><circle cx="6" cy="6" r="6" fill="var(--vine-green)"/></svg>
        www.reviewly.example/biz/vinehollow
      </li>
      <li class="contact-item">
        <svg class="contact-icon" viewBox="0 0 12 12"><circle cx="6" cy="6" r="6" fill="var(--vine-green)"/></svg>
        www.snapgram.example/vinehollowsb
      </li>
    </ul>
  </section>

  <section class="card card-back">
    <div class="brand-lockup">
      <span class="brand-dot"></span>
      <span class="brand-name">Vine Hollow Excursions</span>
    </div>
  </section>

</body>
</html>
```